Marlow Estate Fixers (Handyman / Home Improvement Company)

Looking for a double sided professional looking business card with Logo attached to be highlighted on one side and throwing in an image of a handyman as an option would be nice to see as well. We are a company focused on providing quality Handyman and Home improvement services in a timely manner that is done right the first time with integrity

Industry/Entity Type

Handyman / Home Improvement

Contact Information for Business Card

(LOGO, Name, Mobile and office phone numbers, email) on front side of card, (the words "The SOLUTION to all of your Handyman and Home Improvement needs" followed by "Family Owned and Operated" at the very bottom) on the back.

Colors
EB3D1F
EC4F4E
F09395
F8D3D4
FCEDEE

Requirements
Must have
• Red, Gray, Black Color scheme
Should not have
• No Yellow or Blue colors

```html
<!DOCTYPE html>
<html lang="en">
<head>
<meta charset="utf-8">
<title>Marlow Estate Fixers – Business Card</title>
<link rel="stylesheet" href="https://fonts.googleapis.com/css2?family=Anton&family=Montserrat:wght@400;600;700;800&display=swap">
<style>
  :root {
    --backdrop: #1c1c1c;
    --brand-red: #e8292f;
    --brand-red-deep: #c81f25;
    --ink: #2b2b2b;
    --ink-soft: #444444;
    --rule: #3a3a3a;
    --silver-dark: #9f9f9f;
    --silver-light: #ffffff;
    --white: #ffffff;
  }
  html, body {
    margin: 0;
    padding: 0;
    width: 1200px;
    height: 1059px;
    overflow: hidden;
    background: var(--backdrop);
    font-family: "Montserrat", sans-serif;
  }
  .canvas {
    position: relative;
    width: 1200px;
    height: 1059px;
  }
  .card {
    position: absolute;
    border-radius: 24px;
    overflow: hidden;
    box-shadow: -6px 6px 14px rgba(0,0,0,0.55);
  }

  /* Front side */
  .card-front {
    left: 262px;
    top: 94px;
    width: 714px;
    height: 409px;
    background: linear-gradient(180deg,
      var(--silver-dark) 0%,
      #c9c9c9 28%,
      var(--silver-light) 52%,
      #e6e6e6 66%,
      #c2c2c2 86%,
      #a9a9a9 100%);
  }
  .brand-lockup {
    position: absolute;
    left: 412px;
    top: 38px;
    width: 275px;
    height: 191px;
    display: flex;
    flex-direction: column;
    align-items: center;
    justify-content: center;
    gap: 14px;
  }
  .brand-mark {
    width: 58px;
    height: 58px;
    border-radius: 50%;
    background: var(--brand-red);
  }
  .brand-name {
    font-weight: 800;
    font-size: 24px;
    line-height: 1.15;
    color: var(--brand-red);
    text-align: center;
    letter-spacing: 0.5px;
    text-transform: uppercase;
  }
  .holder-name {
    position: absolute;
    left: 35px;
    top: 253px;
    margin: 0;
    font-weight: 700;
    font-size: 27px;
    color: var(--brand-red);
  }
  .holder-title {
    position: absolute;
    left: 35px;
    top: 298px;
    margin: 0;
    font-weight: 400;
    font-size: 19px;
    color: var(--ink-soft);
  }
  .divider {
    position: absolute;
    left: 36px;
    top: 335px;
    width: 648px;
    height: 2px;
    background: var(--rule);
  }
  .contact-row {
    position: absolute;
    left: 36px;
    top: 352px;
    display: flex;
    align-items: center;
    gap: 20px;
    font-size: 19px;
    color: var(--ink-soft);
    white-space: nowrap;
  }
  .contact-item {
    display: flex;
    align-items: center;
    gap: 10px;
  }
  .contact-icon {
    width: 18px;
    height: 20px;
    fill: var(--brand-red);
  }

  /* Back side */
  .card-back {
    left: 260px;
    top: 529px;
    width: 718px;
    height: 410px;
    background: var(--brand-red);
  }
  .tagline {
    position: absolute;
    left: 20px;
    top: 88px;
    width: 404px;
    margin: 0;
    text-align: center;
    color: var(--white);
  }
  .tagline-lead {
    display: block;
    font-family: "Montserrat", sans-serif;
    font-weight: 700;
    font-size: 28px;
    line-height: 44px;
  }
  .tagline-strong {
    display: block;
    font-family: "Anton", sans-serif;
    font-weight: 400;
    font-size: 46px;
    line-height: 56px;
    letter-spacing: -0.5px;
  }
  .tagline-strong .small {
    font-size: 38px;
  }
  .family-line {
    position: absolute;
    left: 20px;
    top: 354px;
    width: 404px;
    margin: 0;
    text-align: center;
    font-weight: 700;
    font-size: 22px;
    color: var(--white);
  }
  .handyman-art {
    position: absolute;
    left: 417px;
    top: 18px;
    width: 297px;
    height: 382px;
    border-radius: 18px;
    background: linear-gradient(180deg, #d9353a 0%, var(--brand-red-deep) 100%);
  }
</style>
</head>
<body>
<main class="canvas">

  <section class="card card-front" aria-label="Business card front">
    <div class="brand-lockup">
      <div class="brand-mark"></div>
      <div class="brand-name">Marlow Estate<br>Fixers</div>
    </div>

    <h1 class="holder-name">Daniel Harrow</h1>
    <p class="holder-title">Owner</p>
    <div class="divider"></div>

    <div class="contact-row">
      <span class="contact-item">
        <svg class="contact-icon" viewBox="0 0 18 20" aria-hidden="true">
          <path d="M5 0h8a2 2 0 0 1 2 2v16a2 2 0 0 1-2 2H5a2 2 0 0 1-2-2V2a2 2 0 0 1 2-2zm0 2.5v12h8v-12zm4 13.5a1.2 1.2 0 1 0 0 2.4a1.2 1.2 0 0 0 0-2.4z"/>
        </svg>
        044-987 654 321
      </span>
      <span class="contact-item">
        <svg class="contact-icon" viewBox="0 0 20 20" aria-hidden="true">
          <path d="M1 6c0-2 4-4 9-4s9 2 9 4v2h-5V6.5c-1.5-.6-6.5-.6-8 0V8H1z"/>
          <path d="M4 10l2-2h8l2 2v7H4z"/>
        </svg>
        044-987 654 321
      </span>
      <span class="contact-item">
        <svg class="contact-icon" viewBox="0 0 20 16" aria-hidden="true">
          <path d="M0 2h20v12H0z"/>
          <path d="M0 2l10 7l10-7" fill="none" stroke="#ffffff" stroke-width="1.6"/>
        </svg>
        info@marlowfixers.com
      </span>
    </div>
  </section>

  <section class="card card-back" aria-label="Business card back">
    <h2 class="tagline">
      <span class="tagline-lead">Your SOLUTION to all of</span>
      <span class="tagline-strong"><span class="small">your</span> Handyman <span class="small">and</span></span>
      <span class="tagline-strong">Home Improvement</span>
      <span class="tagline-strong">Needs</span>
    </h2>
    <p class="family-line">Family Owned and Operated</p>
    <div class="handyman-art" role="img" aria-label="Cartoon handyman holding a pipe wrench and spanner"></div>
  </section>

</main>
</body>
</html>
```